KELBRIDGE PAINTING

We are a painting company. We paint residential, commercial and strata jobs. I need the website to be very sharp, neat and elegant. I've attached our logo. the Logo needs to be embossed as a gold color and the background like a Matt black. I need these tabs:

• HOME • ABOUT US • SERVICES • TESTIMONIALS • SHOWCASE • CONTACT US

Be creative and innovative in your style.
take this as an example to just get the gist of what I'm expecting. If you can better it then the job is yours!

http://rickhalvorpainting.com.au/contact.html

I look forward to seeing your artwork :)

#These are the links to my logo in PSD format.

https://www.filevaultzy.com/s/qwertplk83nd7ha/Kelbridge%20Painting%20Luxury%20Gold.rar

https://www.filevaultzy.com/sh/bzuyrak2m5wqp9/QoPL7-xvMn

Painting

• Making the Logo embossed like the artworks i have attached is definitely a necessity.

Can you let me know if this is possible to apply to the website.

thank you

```html
<!DOCTYPE html>
<html lang="en">
<head>
<meta charset="utf-8">
<title>Kelbridge Painting</title>
<link rel="stylesheet" href="https://fonts.googleapis.com/css2?family=Source+Sans+3:ital,wght@0,400;0,600;0,700;1,400&display=swap">
<style>
:root{
  --matt:#1e232b;
  --footer:#41464d;
  --gold:#f0c450;
  --gold-deep:#d6a21c;
  --gold-mid:#e3b143;
  --gold-soft:#efc870;
  --gold-pale:#f5d9a0;
  --grey-1:#4a4f57;
  --grey-2:#6c7077;
  --grey-3:#9a9ca0;
  --white:#ffffff;
  --hero-light:#c9a88a;
  --hero-dark:#6e4a33;
}
*{margin:0;padding:0;box-sizing:border-box}
html,body{width:1157px;height:1200px;overflow:hidden;background:var(--matt)}
body{position:relative;font-family:"Source Sans 3",sans-serif;color:var(--white)}
.abs{position:absolute}

.site-header{left:0;top:0;width:1157px;height:89px;background:var(--matt);border-bottom:1px solid var(--gold-deep)}
.phone{right:160px;top:18px;display:flex;align-items:center;gap:9px;color:var(--gold);font-weight:600;font-size:22px;letter-spacing:.2px}
.main-nav{right:159px;top:61px;display:flex;gap:29px;font-weight:600;font-size:14.5px;letter-spacing:.6px}
.main-nav a{color:var(--white);text-decoration:none}
.main-nav a.active{color:var(--gold)}

.hero{left:0;top:89px;width:1157px;height:436px;background:linear-gradient(180deg,#8a6a52 0%,var(--hero-dark) 45%,var(--hero-light) 100%)}
.brand-emblem{left:164px;top:25px;width:104px;height:104px;border-radius:50%;background:var(--matt);border:3px solid var(--gold-deep)}
.brand-band{left:267px;top:90px;width:490px;height:37px;background:linear-gradient(90deg,#f6dc86,#e7b948 60%,#f1cd6c);display:flex;align-items:center;padding-left:16px}
.brand-name{color:var(--matt);font-weight:700;font-size:21px;letter-spacing:1.4px}
.brand-sep{width:1px;height:18px;background:var(--gold-deep);margin:0 14px}
.brand-tagline{color:var(--matt);font-style:italic;font-size:17px}

.slider-dots{left:935px;top:120px;display:flex;gap:9px}
.slider-dots span{width:9px;height:9px;background:#3a3d42}
.slider-dots span.on{background:var(--gold)}

.accent-left{left:159px;top:324px;width:54px;height:52px;background:var(--gold-mid)}
.accent-right{left:641px;top:378px;width:160px;height:98px;background:var(--gold-mid)}
.accent-grey{left:749px;top:333px;width:34px;height:6px;background:#9ea0a4}
.headline-box{left:169px;top:333px;width:614px;height:133px;background:var(--matt);padding:18px 0 0 35px}
.headline-box h1{font-weight:400;font-size:43px;line-height:48px;letter-spacing:-.2px}

.stripe{left:0;width:1157px;height:9px;display:flex}
.stripe span{height:100%}

.about{left:159px;top:568px;width:838px}
.about h2{color:var(--gold);font-weight:600;font-size:41px;line-height:50px;margin-bottom:33px}
.about p{font-size:13.6px;line-height:26.7px;width:530px;margin-bottom:26.7px}
.about p.wide{width:838px}
.about-photo{left:730px;top:592px;width:267px;height:336px;background:#474c54;padding:6px}
.about-photo div{width:100%;height:100%;background:linear-gradient(160deg,#9fb8c8 0%,#a7b4bc 45%,#7d8a92 100%)}

.site-footer{left:0;top:1137px;width:1157px;height:63px;background:var(--footer)}
.copyright{left:162px;top:20px;font-size:12.5px}
.social{left:833px;top:17px;display:flex;gap:16px}
.social span{width:29px;height:29px;border-radius:50%;background:#b9babc}
.social span.first{background:#3b5a94}
</style>
</head>
<body>
<header class="site-header abs">
  <div class="phone abs">
    <svg width="20" height="20" viewBox="0 0 24 24" aria-hidden="true"><path fill="#f0c450" d="M6.6 10.8a15.1 15.1 0 0 0 6.6 6.6l2.2-2.2a1 1 0 0 1 1-.25 11.4 11.4 0 0 0 3.6.57 1 1 0 0 1 1 1V20a1 1 0 0 1-1 1A17 17 0 0 1 3 4a1 1 0 0 1 1-1h3.5a1 1 0 0 1 1 1c0 1.25.2 2.45.57 3.57a1 1 0 0 1-.25 1z"/></svg>
    1300 47 19 52
  </div>
  <nav class="main-nav abs">
    <a class="active" href="#">HOME</a>
    <a href="#">ABOUT US</a>
    <a href="#">SERVICES</a>
    <a href="#">TESTIMONIALS</a>
    <a href="#">SHOWCASE</a>
    <a href="#">CONTACT US</a>
  </nav>
</header>

<section class="hero abs" role="img" aria-label="Photo of a painted living room with a brown and cream leather sofa"></section>

<div class="brand-emblem abs"></div>
<div class="brand-band abs">
  <span class="brand-name">KELBRIDGE PAINTING</span>
  <span class="brand-sep"></span>
  <span class="brand-tagline">Painting Australia Everyday!</span>
</div>

<div class="slider-dots abs"><span></span><span></span><span></span><span class="on"></span></div>

<div class="accent-left abs"></div>
<div class="accent-right abs"></div>
<div class="headline-box abs"><h1>We paint residential,<br>commercial and strata jobs</h1></div>
<div class="accent-grey abs"></div>

<div class="stripe abs" style="top:525px">
  <span style="width:277px;background:var(--matt)"></span>
  <span style="width:79px;background:var(--grey-1)"></span>
  <span style="width:87px;background:var(--grey-2)"></span>
  <span style="width:137px;background:var(--grey-3)"></span>
  <span style="width:116px;background:var(--gold-deep)"></span>
  <span style="width:79px;background:var(--gold-mid)"></span>
  <span style="width:87px;background:var(--gold-soft)"></span>
  <span style="width:295px;background:var(--gold-pale)"></span>
</div>

<main class="about abs">
  <h2>About us</h2>
  <p>Lorem ipsum dolor sit amet, consectetur adipiscing elit. Quantum Aristoxeni ingenium consumptum videmus in musicis? Nihil enim hoc differt. Re mihi non aeque satisfacit, et quidem locis pluribus. At iste non dolendi status non vocatur voluptas. Quamquam haec quidem praeposita recte et reiecta dicere licebit.</p>
  <p>Duo Reges: constructio interrete. Inde sermone vario sex illa a Dipylo stadia confecimus. Ad quorum et cognitionem et usum iam corroborati natura ipsa praeeunte deducimur. Idem iste, inquam, de voluptate quid sentit? Septem autem illi non suo, sed populorum suffragio omnium nominati sunt. Quamquam haec quidem praeposita recte et reiecta dicere licebit. Atqui eorum nihil est eius generis, ut sit in fine atque extrerno bonorum.</p>
  <p class="wide">Lorem ipsum dolor sit amet, consectetur adipiscing elit. Quantum Aristoxeni ingenium consumptum videmus in musicis? Nihil enim hoc differt. Re mihi non aeque satisfacit, et quidem locis pluribus. At iste non dolendi status non vocatur voluptas. Quamquam haec quidem praeposita recte et reiecta dicere licebit.</p>
</main>

<figure class="about-photo abs"><div role="img" aria-label="Photo of a painter on a ladder painting the gable of a weatherboard house"></div></figure>

<div class="stripe abs" style="top:1129px">
  <span style="width:295px;background:var(--gold-pale)"></span>
  <span style="width:87px;background:var(--gold-soft)"></span>
  <span style="width:79px;background:var(--gold-mid)"></span>
  <span style="width:118px;background:var(--gold-deep)"></span>
  <span style="width:135px;background:var(--grey-3)"></span>
  <span style="width:87px;background:var(--grey-2)"></span>
  <span style="width:79px;background:var(--grey-1)"></span>
</div>

<footer class="site-footer abs">
  <p class="copyright abs">Copyright @ 2013 Kelbridge Painting. All rights reserved.</p>
  <div class="social abs" aria-label="Social links">
    <span class="first"></span><span></span><span></span><span></span>
  </div>
</footer>
</body>
</html>
```